BUSINESS CARD DESIGN

NAME- DALE VORSKIN
PHONE NUMER - 555- 714-9082
EMAIL- OFFICE@TRV-GROUNDMAKRZ.COM
BACK OF CARD- SPEACIALIZES IN LAND CLEARING, FORESTRY MUCLHING AND EXCAVATION

Contact Information for Business Card

NAME- DALE VORSKIN PHONE NUMER - 555- 714-9082 EMAIL- OFFICE@TRV-GROUNDMAKRZ.COM BACK OF CARD- SPEACIALIZES IN LAND CLEARING , MUCLHING AND EXCAVATION

```html
<!DOCTYPE html>
<html lang="en">
<head>
<meta charset="utf-8">
<title>Trevara Ground Makrz – Business Card</title>
<link href="https://fonts.googleapis.com/css2?family=Montserrat:wght@400;500;700&display=swap" rel="stylesheet">
<style>
  :root {
    --backdrop: #5e4c39;
    --card: #050505;
    --gold: #f6b418;
    --white: #ffffff;
    --muted: #d9d9d9;
  }
  * { margin: 0; padding: 0; box-sizing: border-box; }
  html, body { width: 900px; height: 1200px; overflow: hidden; }
  body {
    background: var(--backdrop);
    font-family: "Montserrat", sans-serif;
    position: relative;
  }
  .card {
    position: absolute;
    background: var(--card);
    border-radius: 22px;
    box-shadow: 0 10px 24px rgba(0,0,0,.45);
  }
  .card-front { left: 80px; top: 130px; width: 742px; height: 442px; }
  .card-back  { left: 78px; top: 638px; width: 744px; height: 440px; }

  .brand {
    position: absolute;
    display: flex;
    flex-direction: column;
    align-items: center;
    text-align: center;
    font-weight: 700;
    letter-spacing: 2px;
    line-height: 1.25;
  }
  .brand-mark {
    border-radius: 50%;
    border: 5px solid currentColor;
  }
  .brand-gold { color: var(--gold); left: 45px; top: 18px; width: 255px; font-size: 20px; }
  .brand-gold .brand-mark { width: 110px; height: 110px; margin-bottom: 16px; }

  .brand-deco { color: var(--white); left: 410px; top: 165px; width: 300px; font-size: 18px; }
  .brand-deco .brand-mark { width: 170px; height: 170px; margin-bottom: 14px; }

  .brand-back { color: var(--white); left: 172px; top: 52px; width: 400px; font-size: 30px; }
  .brand-back .brand-mark { width: 180px; height: 180px; margin-bottom: 18px; }

  .specialties {
    position: absolute;
    left: 72px; right: 72px; top: 352px;
    text-align: center;
    color: var(--muted);
    font-size: 14px;
    font-weight: 500;
    letter-spacing: 1.5px;
    line-height: 1.6;
  }

  .person { position: absolute; right: 46px; top: 44px; text-align: right; }
  .person-name { color: var(--gold); font-weight: 700; font-size: 24px; letter-spacing: .5px; }
  .person-title { color: var(--muted); font-size: 16px; margin-top: 4px; }

  .contacts { position: absolute; left: 38px; top: 326px; list-style: none; }
  .contacts li {
    display: flex; align-items: center; gap: 10px;
    color: var(--white); font-size: 15.5px; height: 28px;
  }
  .contacts svg { width: 14px; height: 14px; fill: var(--gold); flex: none; }
</style>
</head>
<body>
  <section class="card card-front">
    <div class="brand brand-gold">
      <span class="brand-mark"></span>
      TREVARA GROUND MAKRZ LLC
    </div>

    <div class="person">
      <h1 class="person-name">DALE VORSKIN</h1>
      <p class="person-title">Managing Director</p>
    </div>

    <ul class="contacts">
      <li>
        <svg viewBox="0 0 24 24"><path d="M6.6 10.8a15 15 0 0 0 6.6 6.6l2.2-2.2a1 1 0 0 1 1-.25 11.4 11.4 0 0 0 3.6.57 1 1 0 0 1 1 1V20a1 1 0 0 1-1 1A17 17 0 0 1 3 4a1 1 0 0 1 1-1h3.5a1 1 0 0 1 1 1c0 1.25.2 2.45.57 3.6a1 1 0 0 1-.25 1z"/></svg>
        555- 714-9082
      </li>
      <li>
        <svg viewBox="0 0 24 24"><path d="M2 6l10 6.5L22 6V5H2zM2 8.3V19h20V8.3l-10 6.5z"/></svg>
        OFFICE@TRV-GROUNDMAKRZ.COM
      </li>
      <li>
        <svg viewBox="0 0 24 24"><circle cx="12" cy="12" r="10"/><path d="M2 12h20M12 2c3 3 3 17 0 20M12 2c-3 3-3 17 0 20" stroke="#050505" stroke-width="1.5" fill="none"/></svg>
        WWW.TRV-GROUNDMAKRZ.COM
      </li>
    </ul>

    <div class="brand brand-deco">
      <span class="brand-mark"></span>
      TREVARA GROUND MAKRZ LLC
    </div>
  </section>

  <section class="card card-back">
    <div class="brand brand-back">
      <span class="brand-mark"></span>
      TREVARA GROUND MAKRZ LLC
    </div>
    <p class="specialties">SPECIALIZES IN LAND CLEARING,<br>FORESTRY MULCHING AND EXCAVATION</p>
  </section>
</body>
</html>
```